MRT Property - Business Cards

Looking for a business card & general letterhead, signage etc design for our new logo.

Colours:
000a20
0056a2
00b5ef
0088ce
68cef2

Fonts:
Poppins
Karla

Please keep look and feel of new brand - example in the zip package I sent.

```html
<!DOCTYPE html>
<html lang="en">
<head>
<meta charset="utf-8">
<title>MRT Property – Business Cards</title>
<link rel="stylesheet" href="https://fonts.googleapis.com/css2?family=Poppins:wght@300;400;500;600;700&display=swap">
<style>
  :root {
    --ink: #000a20;
    --navy-card: #0c1226;
    --brand-deep: #0056a2;
    --brand-mid: #0088ce;
    --brand-bright: #00b5ef;
    --brand-soft: #68cef2;
    --paper: #ffffff;
    --stage: #1f1f1f;
  }
  * { box-sizing: border-box; margin: 0; padding: 0; }
  html, body {
    width: 1200px; height: 780px; overflow: hidden;
    background: var(--stage);
    font-family: "Poppins", sans-serif;
  }
  .canvas {
    width: 1200px; height: 780px;
    display: flex; align-items: center; justify-content: center; gap: 40px;
  }
  .card {
    position: relative; width: 540px; height: 309px; overflow: hidden;
    box-shadow: 0 18px 40px rgba(0,0,0,.55);
  }

  /* Front */
  .card--front { background: var(--paper); color: var(--ink); }
  .band { position: absolute; height: 13px; }
  .band--top {
    top: 0; left: 0; width: 250px; background: var(--brand-mid);
    clip-path: polygon(0 0, 100% 0, 96% 100%, 0 100%);
  }
  .band--bottom {
    bottom: 0; right: 0; width: 300px; background: var(--brand-deep);
    clip-path: polygon(3% 0, 100% 0, 100% 100%, 0 100%);
  }
  .identity { position: absolute; top: 44px; left: 26px; padding-left: 14px; }
  .identity::before {
    content: ""; position: absolute; left: 0; top: 4px; width: 7px; height: 26px;
    background: var(--brand-mid);
  }
  .identity__name { font-size: 25px; line-height: 1.1; letter-spacing: -.2px; }
  .identity__first { font-weight: 600; color: var(--brand-deep); }
  .identity__last { font-weight: 300; color: var(--brand-soft); }
  .identity__role { font-size: 11px; font-weight: 500; margin-top: 1px; }

  .contacts { position: absolute; top: 118px; left: 26px; list-style: none; }
  .contacts li {
    display: flex; align-items: center; gap: 9px;
    font-size: 11.5px; line-height: 19px;
  }
  .contacts svg { width: 11px; height: 11px; fill: var(--brand-mid); flex: none; }

  .wordmark {
    position: absolute; top: 118px; right: 34px;
    display: flex; align-items: center; gap: 10px;
    font-size: 30px; font-weight: 600; color: var(--brand-deep); letter-spacing: -.3px;
  }
  .wordmark__dot { width: 14px; height: 14px; border-radius: 50%; background: var(--brand-mid); }

  .address {
    position: absolute; right: 30px; bottom: 28px; text-align: right;
    font-style: normal; font-size: 13px; line-height: 19px; font-weight: 500;
  }

  /* Back */
  .card--back { background: linear-gradient(160deg, #11172e 0%, var(--navy-card) 60%, #0a0f20 100%); }
  .card--back .wordmark {
    top: auto; bottom: 42px; right: 40px; font-size: 26px;
  }
</style>
</head>
<body>
<main class="canvas">
  <section class="card card--front" aria-label="Business card front">
    <div class="band band--top"></div>
    <div class="band band--bottom"></div>

    <header class="identity">
      <h1 class="identity__name"><span class="identity__first">Callum</span> <span class="identity__last">Reeves</span></h1>
      <p class="identity__role">Director</p>
    </header>

    <ul class="contacts">
      <li>
        <svg viewBox="0 0 24 24" aria-hidden="true"><path d="M6.6 10.8a15.1 15.1 0 0 0 6.6 6.6l2.2-2.2a1 1 0 0 1 1-.25 11.4 11.4 0 0 0 3.6.57 1 1 0 0 1 1 1V20a1 1 0 0 1-1 1A17 17 0 0 1 3 4a1 1 0 0 1 1-1h3.5a1 1 0 0 1 1 1c0 1.25.2 2.45.57 3.57a1 1 0 0 1-.25 1z"/></svg>
        +61 2 9555 0142
      </li>
      <li>
        <svg viewBox="0 0 24 24" aria-hidden="true"><path d="M12 2a10 10 0 1 0 0 20 10 10 0 0 0 0-20zm6.9 6h-2.9a15.6 15.6 0 0 0-1.4-3.6A8 8 0 0 1 18.9 8zM12 4c.8 1.2 1.5 2.5 1.9 4h-3.8c.4-1.5 1.1-2.8 1.9-4zM4.3 14a8.2 8.2 0 0 1 0-4h3.4a16 16 0 0 0 0 4zm.8 2h2.9c.3 1.3.8 2.5 1.4 3.6A8 8 0 0 1 5.1 16zM8 8H5.1a8 8 0 0 1 4.3-3.6C8.8 5.5 8.3 6.7 8 8zm4 12c-.8-1.2-1.5-2.5-1.9-4h3.8c-.4 1.5-1.1 2.8-1.9 4zm2.3-6H9.7a14.7 14.7 0 0 1 0-4h4.6a14.7 14.7 0 0 1 0 4zm.3 5.6c.6-1.1 1.1-2.3 1.4-3.6h2.9a8 8 0 0 1-4.3 3.6zm1.7-5.6a16 16 0 0 0 0-4h3.4a8.2 8.2 0 0 1 0 4z"/></svg>
        www.mrtproperty.com.au
      </li>
      <li>
        <svg viewBox="0 0 24 24" aria-hidden="true"><path d="M20 4H4a2 2 0 0 0-2 2v12a2 2 0 0 0 2 2h16a2 2 0 0 0 2-2V6a2 2 0 0 0-2-2zm0 4-8 5-8-5V6l8 5 8-5z"/></svg>
        info@mrtproperty.com.au
      </li>
    </ul>

    <div class="wordmark"><span class="wordmark__dot"></span>MRT Property</div>

    <address class="address">
      Suite 4.12, Level 3<br>
      18 Harbourline Road<br>
      Rosehill Park NSW 2142
    </address>
  </section>

  <section class="card card--back" aria-label="Business card back">
    <div class="wordmark">MRT Property</div>
  </section>
</main>
</body>
</html>
```